Custom Woodworking and Rock Design

We specialize in original, high quality, wood and rock art. It’s should be self explanatory ask questions if you need. Your team designing a logo. Furniture is custom made to order. Rocks are designed depending on consumer needs. Wood and rock can also be combined for custom work. Painted rocks on vintage wood. Custom chairs and cabinets. Artistic rocks for multiple uses:garden, magnets, custom. All ideas and requests are welcome.

Target Market(s)

All

Contact Information for Business Card

Mara Voss
Talbertstonecraft@mailbrook.net

Font styles to use
Sans Serif

Requirements
Must have
• Clear lettering
Nice to have
• Eye catching
Should not have
• Blurr

```html
<!DOCTYPE html>
<html lang="en">
<head>
<meta charset="UTF-8">
<title>Mara Voss – Business Card</title>
<link rel="stylesheet" href="https://fonts.googleapis.com/css2?family=Open+Sans:wght@400;600&display=swap">
<style>
  :root {
    --page-bg: #d9d6d2;
    --wood-dark: #2f241e;
    --wood-mid: #43352c;
    --wood-light: #54443a;
    --photo-fence: #6e625a;
    --photo-soil: #5a4b40;
    --photo-stone: #8d867e;
    --name-blue: #2fa3d6;
    --email-white: #f2f0ee;
  }
  * { margin: 0; padding: 0; box-sizing: border-box; }
  html, body {
    width: 1200px;
    height: 900px;
    overflow: hidden;
    background: var(--page-bg);
  }
  .canvas {
    width: 1200px;
    height: 900px;
    display: flex;
    align-items: center;
    justify-content: center;
  }
  .business-card {
    width: 1050px;
    height: 600px;
    display: flex;
    overflow: hidden;
    box-shadow: 0 10px 30px rgba(0,0,0,0.25);
  }
  .wood-panel {
    width: 58%;
    height: 100%;
    background:
      linear-gradient(180deg, rgba(255,255,255,0.03), rgba(0,0,0,0.12)),
      linear-gradient(100deg, var(--wood-mid) 0%, var(--wood-dark) 35%, var(--wood-light) 60%, var(--wood-dark) 100%);
    display: flex;
    flex-direction: column;
    justify-content: center;
    align-items: center;
    padding-bottom: 60px;
    font-family: "Open Sans", sans-serif;
  }
  .contact-name {
    color: var(--name-blue);
    font-weight: 600;
    font-size: 46px;
    letter-spacing: 1px;
    line-height: 1.2;
  }
  .contact-email {
    color: var(--email-white);
    font-weight: 400;
    font-size: 27px;
    letter-spacing: 0.5px;
    margin-top: 6px;
  }
  .photo-panel {
    width: 42%;
    height: 100%;
    background: linear-gradient(180deg,
      var(--photo-fence) 0%,
      var(--photo-fence) 28%,
      var(--photo-soil) 40%,
      var(--photo-stone) 70%,
      var(--photo-soil) 88%,
      #b9b4ae 100%);
  }
</style>
</head>
<body>
  <main class="canvas">
    <article class="business-card">
      <section class="wood-panel">
        <p class="contact-name">Mara Voss</p>
        <p class="contact-email">Talbertstonecraft@mailbrook.net</p>
      </section>
      <div class="photo-panel" role="img" aria-label="Photo of a garden bed with large stones in front of a wooden fence and a flag made of painted rocks"></div>
    </article>
  </main>
</body>
</html>
```